Book Cover for a book on Quiet Ventures

I am self-publishing my book on Brindlecart and need a book cover made. Below are the details. See attached templates for size we need to use. I also attached a previous cover we had made that I liked. The problem with it was they were two boys helping each other but the book is about women. I'm open to your ideas on the cover though, but I wanted to show you a style I liked as an idea.
Front of Cover
Book Title: Quiet Ventures
Book Subtitle: Unvarnished Notes of a Woman Founder
Author Name: Lorna T. Pelham
Add on the Spine of Cover: Quiet Ventures and Lorna T. Pelham
Back of the Cover Text:
Quiet Ventures: Unvarnished Notes of a Woman Founder is an honest account of a business owner’s experience attempting to navigate the start-up community while also pursuing spiritual growth. Author Lorna Pelham defines a spiritual entrepreneur as “someone who runs an enterprise with the purpose of growing love rather than material gain.” This book discusses the three dimensions of Quiet Ventures:
1. The business is an integral part of the founder’s spiritual journey.
2. Employees working for the spiritual enterprise, whether they know it or not, encounter this company because it's part of their spiritual path.
3. The business itself has a life force of its own and its purpose is to further the kingdom of heaven on earth.
These three dimensions happen simultaneously and work together to produce the greatest possible result. However, this can feel confusing to a founder juggling these dimensions while also trying to manage and run a business. This is not a formulaic self-help book or roadmap. Rather, it is a compilation of personal reflections that often seem at odds with the traditional world of entrepreneurship.
Below the description add my picture (see attached for my picture)
Bio text:
Lorna Pelham founded Halvex with the vision of ushering in a life-long education system that shifts away from standardization to one that empowers people to live their purpose. In college, Lorna interned for Open Meadow, a women’s empowerment initiative where she recognized her passion for helping people find their voice. Lorna's 20-year journey has come full circle to empowering other female CEOs who are pursuing the path of Quiet Ventures.
NOTE: Please note that Brindlecart puts a bar code on the bottom right of the back cover as is noted on the attached template.
Size template is attached to the brief, here are the sizes typed out:
# Description Width (in) Height (in)
1 Full Cover 12.79 9.25
2 Front Cover 6 9
3 Safe Area 5.875 8.75
4 Bleed 0.125 0.125
5 Margin 0.125 0.125
6 Spine 0.54 9
7 Spine Safe Area 0.415 8.75
8 Spine Margin 0.062 0.062
9 Barcode Margin 0.25 0.25
Pre-publication checklist
BRINDLECART TIPS for the final cover:
1. Save as a PDF. Your cover must be a single PDF that includes the back cover, spine, and front cover as one image.
2. Flatten all transparencies. These can cause the file to print with missing or distorted content. Consult your software's documentation to learn how.
3. Embed your fonts. Consult your software's documentation to learn how.
4. Remove crop marks, color bars, template text. Crop marks are lines showing where pages should be trimmed. Color bars are strips with a series of patches used to ensure color balance during printing. Also, remove any template text, PDF creation guides, or software references.
5. Ensure your cover image meets the minimum resolution of 300 DPI (dots per inch).
6. Optimize PDFs. Optimization is useful to reduce your file size, allowing for higher performance when transferring, uploading, viewing, and printing the files.
7. Remove file security. Locked or encrypted files will fail review.
Target Market(s)
Women who want to be CEOs or are currently CEOs of companies.
Industry/Entity Type
Entrepreneurship, business, spirituality
Requirements
Must have
- Just the text on the description. A very welcoming feel.
Nice to have
- I like the idea of having a sunrise/sunset in the image somehow like in the example I attached to the brief, but again I'm open.
Should not have
- Please don't put any yoga or meditation poses or hands outstretched. I have a lot of interesting ones that look like my example so if you are going to submit after Saturday 10/29, please only do so if you have a new idea! Thanks!

```html
<!DOCTYPE html>
<html lang="en">
<head>
<meta charset="utf-8">
<title>Quiet Ventures – Book Cover</title>
<link href="https://fonts.googleapis.com/css2?family=Noto+Serif:ital,wght@0,400;1,400&display=swap" rel="stylesheet">
<style>
  :root {
    --navy-deep: #0b1a28;
    --navy-mid: #12364d;
    --navy-glow: #1b4e6a;
    --gold: #f7d617;
    --ink-light: #f2f2f0;
    --sky-top: #6f9cc4;
    --sky-glow: #f3ec9a;
    --sun: #f6d94a;
    --city-shadow: #2e3540;
  }
  html, body {
    margin: 0;
    padding: 0;
    width: 1200px;
    height: 874px;
    overflow: hidden;
    background: var(--navy-deep);
  }
  .cover {
    position: relative;
    width: 1200px;
    height: 874px;
    font-family: "Noto Serif", Georgia, serif;
    color: var(--ink-light);
    overflow: hidden;
  }
  .back {
    position: absolute;
    left: 0; top: 0;
    width: 637px; height: 874px;
    background: radial-gradient(ellipse 420px 460px at 300px 420px, var(--navy-glow) 0%, var(--navy-mid) 40%, var(--navy-deep) 100%);
  }
  .blurb {
    position: absolute;
    left: 37px; top: 58px;
    width: 502px;
    font-size: 13.4px;
    line-height: 16.9px;
    letter-spacing: 0.07em;
    text-align: justify;
    hyphens: auto;
  }
  .blurb p { margin: 0 0 16.9px; }
  .blurb .lead { color: var(--gold); }
  .blurb ol {
    margin: 0 0 16.9px;
    padding: 0 0 0 46px;
    list-style: none;
  }
  .blurb li { margin-bottom: 16.9px; }
  .author-photo {
    position: absolute;
    left: 37px; top: 484px;
    width: 124px; height: 124px;
    background: linear-gradient(180deg, #f4f1ee 0%, #e7d9d2 55%, #d95077 100%);
  }
  .bio {
    position: absolute;
    left: 184px; top: 481px;
    width: 363px;
    font-size: 13.4px;
    line-height: 16.9px;
    letter-spacing: 0.07em;
    text-align: justify;
    margin: 0;
  }
  .spine {
    position: absolute;
    left: 572px; top: 0;
    width: 64px; height: 874px;
  }
  .spine-text {
    position: absolute;
    white-space: nowrap;
    transform-origin: left top;
    transform: rotate(90deg);
  }
  .spine-title {
    left: 625px; top: 103px;
    font-size: 25px;
    color: var(--gold);
    letter-spacing: 0.02em;
  }
  .spine-subtitle {
    left: 597px; top: 165px;
    font-size: 17px;
    font-style: italic;
    letter-spacing: 0.04em;
  }
  .spine-author {
    left: 613px; top: 620px;
    font-size: 20px;
    letter-spacing: 0.12em;
  }
  .front {
    position: absolute;
    left: 637px; top: 0;
    width: 563px; height: 874px;
    background: var(--navy-deep);
  }
  .front-art {
    position: absolute;
    left: 0; top: 0;
    width: 563px; height: 560px;
    background:
      radial-gradient(ellipse 200px 160px at 270px 400px, var(--sun) 0%, rgba(246,217,74,0.35) 45%, rgba(246,217,74,0) 100%),
      linear-gradient(180deg, var(--sky-top) 0%, #b9cfd2 28%, var(--sky-glow) 55%, #8c8a6e 72%, var(--city-shadow) 88%, var(--navy-deep) 100%);
  }
  .front-title {
    position: absolute;
    left: 0; top: 570px;
    width: 563px;
    margin: 0;
    text-align: center;
    color: var(--gold);
    font-weight: 400;
    font-size: 46px;
    line-height: 52px;
    letter-spacing: 0.08em;
  }
  .front-subtitle {
    position: absolute;
    left: 0; top: 672px;
    width: 563px;
    margin: 0;
    text-align: center;
    font-style: italic;
    font-size: 24px;
    letter-spacing: 0.04em;
  }
  .front-author {
    position: absolute;
    left: 0; top: 806px;
    width: 563px;
    margin: 0;
    text-align: center;
    font-size: 30px;
    letter-spacing: 0.12em;
  }
</style>
</head>
<body>
<main class="cover">
  <section class="back">
    <div class="blurb">
      <p><span class="lead">QUIET VENTURES:</span> Unvarnished Notes of a Woman Founder is an honest account of a business owner’s experience attempting to navigate the start-up community while also pursuing spiritual growth. Author Lorna Pelham defines a spiritual entrepreneur as “someone who runs an enterprise with the purpose of growing love rather than material gain.” This book discusses the three dimensions of Quiet Ventures:</p>
      <ol>
        <li>1. The business is an integral part of the founder’s spiritual journey.</li>
        <li>2. Employees working for the spiritual enterprise, whether they know it or not, encounter this company because it's part of their spiritual path.</li>
        <li>3. The business itself has a life force of its own and its purpose is to further the kingdom of heaven on earth.</li>
      </ol>
      <p>These three dimensions happen simultaneously and work together to produce the greatest possible result. However, this can feel confusing to a founder juggling these dimensions while also trying to manage and run a business. This is not a formulaic self-help book or roadmap. Rather, it is a compilation of personal reflections that often seem at odds with the traditional world of entrepreneurship.</p>
    </div>
    <div class="author-photo" role="img" aria-label="Portrait photo of the author"></div>
    <p class="bio">Lorna Pelham founded Halvex with the vision of ushering in a life-long education system that shifts away from standardization to one that empowers people to live their purpose. In college, Lorna interned for Open Meadow, a women’s empowerment initiative where she recognized her passion for helping people find their voice. Lorna's 20-year journey has come full circle to empowering other female CEOs who are pursuing the path of Quiet Ventures.</p>
  </section>

  <section class="spine" aria-label="Spine"></section>
  <div class="spine-text spine-title">QUIET VENTURES</div>
  <div class="spine-text spine-subtitle">Unvarnished Notes of a Woman Founder</div>
  <div class="spine-text spine-author">Lorna T. Pelham</div>

  <section class="front">
    <div class="front-art" role="img" aria-label="Photo of a woman in silhouette standing on a rooftop ledge between city towers at sunrise"></div>
    <h1 class="front-title">QUIET<br>VENTURES</h1>
    <p class="front-subtitle">Unvarnished Notes of a Woman Founder</p>
    <p class="front-author">Lorna T. Pelham</p>
  </section>
</main>
</body>
</html>
```